Diabetes control Orbis/Verdant app design

I need a modern app design with light colors that are easy on the eyes, This app is for diabetes control. Focusing on Sweet/carb control and its daily intake .. I have uploaded some wireframe pages to design . Light colors are preferred for design. I donot need too much Hussle and data on main page.
Name/title: Glimwell- Diabetes reversal

Target Market(s)

Diabetes patients

Industry/Entity Type

health

Colors
0094D4
00A9DD
6FCCEA
C7EBF8
E9F6FB
00AB8E
00BBA5
67D7C9
C6EFE9
E9F9F6
59FF00
82FF00
B8FF75
E3FFCB
F4FFEA
FFC000
F8CF3A
FAE287
FDF2CF
FEFAEE

Requirements
Should not have
• complicated design. It should be simple , modern and easy o eye.

```html
<!DOCTYPE html>
<html lang="en">
<head>
<meta charset="utf-8">
<title>Glimwell – Diabetes Control App Design</title>
<link rel="stylesheet" href="https://fonts.googleapis.com/css2?family=Inter:wght@400;500;600;700;800&display=swap">
<style>
:root{
  --blue:#0094D4;--sky:#00A9DD;--light:#6FCCEA;--pale:#C7EBF8;--mist:#E9F6FB;
  --page:#efefef;--screen:#f4f7fb;--card:#ffffff;--ink:#1f1f1f;--text:#333a40;--muted:#9aa3ad;
  --line:#e3e9f0;--field:#f2f4f7;
}
*{box-sizing:border-box;margin:0;padding:0}
html,body{width:1200px;height:3000px;overflow:hidden}
body{background:var(--page);font-family:"Inter",sans-serif;color:var(--text);position:relative}
.page-title{position:absolute;top:92px;left:0;width:1200px;text-align:center;font-size:43px;font-weight:800;color:#111;letter-spacing:-.5px}
.specs{position:absolute;top:190px;left:495px;display:flex;gap:74px}
.spec-label{font-size:18px;color:#9a9a9a;letter-spacing:.5px}
.spec-value{margin-top:14px;font-size:23px;font-weight:500;color:#222}
.tool-chip{margin-top:10px;display:flex;align-items:center;gap:8px;font-size:14px;font-weight:500;color:#222}
.tool-chip i{width:34px;height:34px;border-radius:8px;background:#fff;display:block}
.hero{position:absolute;top:320px;left:0;width:1200px;height:560px;background:#e7e7e7}
.hero-frame{position:absolute;overflow:hidden;border-radius:20px;background:var(--screen);box-shadow:0 8px 24px rgba(0,0,0,.08)}
.hero-frame .screen{position:absolute;top:0;left:0;transform-origin:0 0;box-shadow:none}
.section-label{position:absolute;font-size:11px;font-weight:600;color:#333;letter-spacing:.3px;text-align:center;width:250px}
.screen{position:absolute;width:250px;background:var(--screen);border-radius:22px;overflow:hidden;box-shadow:0 6px 20px rgba(0,0,0,.07)}
.screen-top{position:absolute;inset:0 0 auto 0;height:170px;background:linear-gradient(180deg,#eef3fa,#f4f7fb)}
.status{position:relative;height:24px;display:flex;justify-content:space-between;align-items:center;padding:0 14px;font-size:7.5px;color:var(--muted)}
.status-icons{display:flex;gap:4px}
.status-icons i{display:block;width:8px;height:5px;background:#b9c0c8;border-radius:1px}
.appbar{position:relative;height:36px;display:flex;align-items:center;padding:0 14px}
.appbar .title{flex:1;text-align:center;font-size:12.5px;font-weight:500;color:var(--ink)}
.icon{width:12px;height:12px;flex:none}
.avatar{width:20px;height:20px;border-radius:50%;background:radial-gradient(circle at 50% 40%,#b88a6a,#5a3e30);border:2px solid #c94a3a;margin-left:8px;flex:none}
.nav{position:absolute;left:0;right:0;bottom:0;height:46px;display:flex;justify-content:space-around;align-items:center;background:var(--screen);padding:0 8px}
.nav svg{width:16px;height:16px;color:#b7bec7}
.nav .active{position:relative}
.nav .active svg{color:var(--blue)}
.nav .active::after{content:"";position:absolute;left:6px;bottom:-8px;width:4px;height:4px;border-radius:50%;background:var(--blue)}
.ring-wrap{position:relative;margin:12px auto 0;width:138px;height:138px;border-radius:50%;background:radial-gradient(circle,#fff 52%,#e6edf5 53%,#eef3f9 70%,transparent 71%)}
.ring-wrap svg{position:absolute;inset:14px;width:110px;height:110px}
.ring-value{position:absolute;inset:0;display:flex;flex-direction:column;align-items:center;justify-content:center}
.ring-value b{font-size:40px;font-weight:700;color:var(--blue);line-height:1}
.ring-value small{font-size:7px;color:var(--muted);text-align:center;line-height:1.5;margin-top:4px}
.heading{font-size:12px;font-weight:500;color:var(--ink);text-align:center}
.gauge{display:block;margin:8px auto 0;width:200px;height:170px}
.card{background:var(--card);border-radius:10px;margin:0 10px 10px;padding:10px}
.card-title{font-size:9.5px;font-weight:500;text-align:center;color:var(--ink);margin-bottom:8px}
.chart{display:flex;gap:4px}
.y-axis{display:flex;flex-direction:column;justify-content:space-between;font-size:6.5px;color:#444;padding-bottom:14px}
.chart-body{flex:1}
.chart-body svg{display:block;width:100%}
.x-axis{display:flex;justify-content:space-between;font-size:6.5px;color:#b5bcc4;margin-top:4px}
.stats{display:flex;gap:8px;margin:0 10px}
.stat{flex:1;background:var(--card);border-radius:8px;display:flex;align-items:center;gap:6px;padding:7px 8px;font-size:7.5px;line-height:1.3}
.stat-dot{width:22px;height:22px;border-radius:50%;display:flex;align-items:center;justify-content:center;color:#fff;font-size:9px;font-weight:600;flex:none}
.feed{background:var(--card);border-radius:8px;margin:0 10px 10px;padding:9px 10px}
.feed-label{display:flex;align-items:center;gap:6px;font-size:7.5px;color:var(--muted)}
.feed-label svg{width:14px;height:14px;color:var(--blue)}
.feed-field{margin-top:7px;background:var(--field);border-radius:5px;padding:6px 8px;font-size:10px;color:var(--ink)}
.feed-field small{font-size:6.5px;color:var(--muted)}
.info-card{margin:14px 12px 0;border:1px solid var(--light);background:var(--mist);border-radius:8px;display:flex;align-items:center;gap:10px;padding:10px 12px;font-size:9.5px;line-height:1.55;color:var(--ink)}
.flame-badge{width:26px;height:26px;border-radius:50%;background:var(--blue);flex:none}
.sub{font-size:8.5px;text-align:center;color:#444;margin-top:14px}
.stepper{display:flex;align-items:center;margin:14px 24px 0}
.stepper i{width:8px;height:8px;border-radius:50%;background:#d7dee6;flex:none;display:block}
.stepper i.done{width:10px;height:10px;background:var(--blue)}
.stepper i.now{background:var(--blue);box-shadow:0 0 0 3px var(--pale)}
.stepper b{flex:1;height:2px;background:#dfe5ec;display:block}
.stepper b.done{background:var(--blue)}
.date-card{background:var(--card);border-radius:8px;margin:16px 10px 0;padding:14px 10px 10px;font-size:9px;color:#333}
.date-field{margin-top:10px;background:var(--field);border-radius:5px;padding:8px;display:flex;justify-content:space-between;align-items:center;font-size:9px}
.buttons{position:absolute;left:12px;right:12px;display:flex;gap:14px}
.btn{flex:1;height:27px;border-radius:5px;display:flex;align-items:center;justify-content:center;font-size:8.5px;font-weight:600}
.btn-ghost{border:1px solid var(--light);color:var(--blue);background:#fff}
.btn-main{background:var(--sky);color:#fff}
.diet{background:var(--card);border-radius:8px;margin:0 10px 8px;padding:8px 10px;display:flex;align-items:center;gap:10px;font-size:9.5px;color:var(--ink)}
.diet-photo{width:28px;height:28px;border-radius:6px;flex:none}
.diet .check{margin-left:auto;width:14px;height:14px;border-radius:50%;background:#eef1f4}
.diet .check.on{background:var(--blue)}
.reason{font-size:8.5px;line-height:1.9;color:#555;background:var(--mist);border-radius:6px;padding:8px 10px}
.pill{margin:0 10px 10px;border:1px solid var(--light);background:var(--mist);border-radius:8px;padding:9px 10px;display:flex;align-items:center;gap:8px;font-size:8px;color:var(--ink)}
.pill i{width:16px;height:16px;border-radius:50%;background:var(--blue);display:block}
.mini-rings{display:flex;justify-content:space-around}
.mini{display:flex;flex-direction:column;align-items:center;gap:4px;font-size:6.5px;color:var(--muted)}
.mini div{width:30px;height:30px;border-radius:50%;border:2.5px solid var(--sky);border-right-color:var(--pale);display:flex;align-items:center;justify-content:center;font-size:10px;font-weight:600;color:var(--blue)}
.streak-ring{width:90px;height:90px;border-radius:50%;margin:6px auto 0;border:2px solid var(--pale);display:flex;align-items:center;justify-content:center}
.flame{width:50px;height:58px;border-radius:50% 50% 46% 46%;background:radial-gradient(circle at 50% 70%,#ffd23a,#f7601f 60%,#e93b1b)}
.streak-num{font-size:32px;font-weight:700;text-align:center;color:#111;line-height:1;margin-top:-14px;position:relative}
.streak-label{font-size:10px;font-weight:500;text-align:center;color:#111;margin-top:4px}
.best{margin:12px 6px 4px;border:1px solid var(--light);border-radius:8px;padding:8px;display:flex;align-items:center;justify-content:center;gap:10px;font-size:8px;color:var(--ink)}
.best i{width:12px;height:14px;border-radius:50% 50% 45% 45%;background:var(--blue);display:block}
.best b{color:var(--blue);font-weight:600}
.thanks{position:absolute;top:2880px;left:0;width:1200px;text-align:center;font-size:44px;font-weight:800;color:#e4e4e4;letter-spacing:.5px}
</style>
</head>
<body>

<svg width="0" height="0" style="position:absolute" aria-hidden="true">
  <defs>
    <linearGradient id="areaFill" x1="0" y1="0" x2="0" y2="1"><stop offset="0" stop-color="#6FCCEA" stop-opacity=".35"/><stop offset="1" stop-color="#6FCCEA" stop-opacity="0"/></linearGradient>
    <linearGradient id="barFill" x1="0" y1="0" x2="0" y2="1"><stop offset="0" stop-color="#00A9DD"/><stop offset="1" stop-color="#0094D4"/></linearGradient>
    <linearGradient id="greenArc" x1="0" y1="1" x2="0" y2="0"><stop offset="0" stop-color="#b9f5b0"/><stop offset="1" stop-color="#59d86a"/></linearGradient>
    <linearGradient id="redArc" x1="0" y1="0" x2="0" y2="1"><stop offset="0" stop-color="#ffb1b6"/><stop offset="1" stop-color="#ef4a58"/></linearGradient>
    <linearGradient id="blueArc" x1="0" y1="0" x2="1" y2="0"><stop offset="0" stop-color="#dceefa"/><stop offset="1" stop-color="#b6d8f2"/></linearGradient>
  </defs>
  <symbol id="i-menu" viewBox="0 0 12 12"><path d="M2 3h8M2 6h6M2 9h8" stroke="#555" stroke-width="1.2" fill="none" stroke-linecap="round"/></symbol>
  <symbol id="i-bell" viewBox="0 0 12 12"><path d="M3 8.5V5.5a3 3 0 0 1 6 0v3l1 1H2z M5 10.5h2" fill="#333"/></symbol>
  <symbol id="n-pie" viewBox="0 0 16 16"><path d="M7 2.5a5.5 5.5 0 1 0 6.5 6.5H7z M9 1.5v5.5h5.5A5.5 5.5 0 0 0 9 1.5z" fill="none" stroke="currentColor" stroke-width="1.3"/></symbol>
  <symbol id="n-cols" viewBox="0 0 16 16"><rect x="2" y="2.5" width="12" height="11" rx="1.5" fill="none" stroke="currentColor" stroke-width="1.3"/><path d="M6 2.5v11M10 2.5v11" stroke="currentColor" stroke-width="1.3"/></symbol>
  <symbol id="n-target" viewBox="0 0 16 16"><circle cx="8" cy="8" r="6" fill="none" stroke="currentColor" stroke-width="1.3"/><circle cx="8" cy="8" r="3.2" fill="none" stroke="currentColor" stroke-width="1.3"/></symbol>
  <symbol id="n-board" viewBox="0 0 16 16"><rect x="2" y="2.5" width="12" height="11" rx="1.5" fill="none" stroke="currentColor" stroke-width="1.3"/><path d="M2 5.5h12M6 5.5v5M10 5.5v3" stroke="currentColor" stroke-width="1.3"/></symbol>
  <symbol id="n-user" viewBox="0 0 16 16"><circle cx="8" cy="5.5" r="3" fill="none" stroke="currentColor" stroke-width="1.3"/><path d="M2.5 14c.5-3 2.8-4.5 5.5-4.5s5 1.5 5.5 4.5z" fill="none" stroke="currentColor" stroke-width="1.3"/></symbol>
  <symbol id="line-chart" viewBox="0 0 180 80">
    <path d="M0 70 C8 62,14 62,20 66 C28 72,30 40,38 42 C46 44,44 76,52 72 C62 66,66 14,80 8 C92 2,96 44,106 48 C114 52,118 34,126 38 C134 42,132 62,142 64 L180 66 L180 80 L0 80Z" fill="url(#areaFill)"/>
    <path d="M0 70 C8 62,14 62,20 66 C28 72,30 40,38 42 C46 44,44 76,52 72 C62 66,66 14,80 8 C92 2,96 44,106 48 C114 52,118 34,126 38 C134 42,132 62,142 64 L180 66" fill="none" stroke="#00A9DD" stroke-width="1.6"/>
  </symbol>
  <symbol id="bar-chart" viewBox="0 0 180 100">
    <rect x="4" y="30" width="14" height="70" fill="url(#barFill)"/>
    <rect x="30" y="12" width="14" height="88" fill="url(#barFill)"/>
    <rect x="56" y="0" width="14" height="100" fill="url(#barFill)"/>
    <rect x="82" y="52" width="14" height="48" fill="url(#barFill)"/>
    <rect x="108" y="28" width="14" height="72" fill="url(#barFill)"/>
    <rect x="134" y="6" width="14" height="94" fill="url(#barFill)"/>
    <rect x="160" y="75" width="14" height="25" fill="url(#barFill)"/>
  </symbol>
  <symbol id="gauge" viewBox="0 0 200 170">
    <path d="M57.6 150.6 A66 66 0 0 1 49.4 57.6" fill="none" stroke="url(#greenArc)" stroke-width="30"/>
    <path d="M53.3 53.3 A66 66 0 0 1 146.7 53.3" fill="none" stroke="url(#blueArc)" stroke-width="30"/>
    <path d="M150.6 57.6 A66 66 0 0 1 142.4 150.6" fill="none" stroke="url(#redArc)" stroke-width="30"/>
    <circle cx="100" cy="100" r="30" fill="#fff" stroke="#e5ecf3" stroke-width="2"/>
    <path d="M100 48 L94 74 L106 74Z" fill="#0094D4"/>
    <text x="100" y="111" text-anchor="middle" font-family="Inter,sans-serif" font-size="30" font-weight="600" fill="#0094D4">4</text>
    <text x="100" y="43" text-anchor="middle" font-family="Inter,sans-serif" font-size="8" letter-spacing="2.5" fill="#333">FATAL</text>
    <text transform="translate(44 110) rotate(-78)" text-anchor="middle" font-family="Inter,sans-serif" font-size="7.5" letter-spacing="2.5" fill="#333">DANGER</text>
    <text transform="translate(157 104) rotate(82)" text-anchor="middle" font-family="Inter,sans-serif" font-size="7" letter-spacing="1" fill="#333">CATASTROPHIC</text>
  </symbol>
</svg>

<h1 class="page-title">DIABETES CONTROL ORBIS/VERDANT APP DESIGN</h1>
<div class="specs">
  <div><div class="spec-label">FONTS</div><div class="spec-value">INTER</div></div>
  <div><div class="spec-label">TOOLS</div><div class="tool-chip"><i></i>Frameset</div></div>
</div>

<!-- Overview strip -->
<div class="hero">
  <div class="hero-frame" style="left:100px;top:60px;width:140px;height:440px">
    <div class="screen" style="height:786px;transform:scale(.56)">
      <div class="status"><span>12:30PM</span><span class="status-icons"><i></i><i></i><i></i></span></div>
      <div class="appbar"><svg class="icon"><use href="#i-menu"/></svg><span class="title">Goals</span><svg class="icon"><use href="#i-bell"/></svg><span class="avatar" role="img" aria-label="User portrait"></span></div>
      <div class="card" style="margin-top:10px"><div class="card-title">Days Until Goal</div><div class="mini-rings"><div class="mini"><div>10</div>Days</div><div class="mini"><div>5</div>Hour</div><div class="mini"><div>25</div>Mins</div><div class="mini"><div>50</div>Sec</div></div></div>
      <div class="card" style="padding:16px 10px"><div class="streak-ring"><div class="flame" role="img" aria-label="Flame illustration"></div></div><div class="streak-num">8</div><div class="streak-label">Days Streak</div><div class="best"><i></i>Your Best Streak : <b>20 Days</b></div></div>
      <nav class="nav"><span class="active"><svg><use href="#n-pie"/></svg></span><svg><use href="#n-cols"/></svg><svg><use href="#n-target"/></svg><svg><use href="#n-board"/></svg><svg><use href="#n-user"/></svg></nav>
    </div>
  </div>
  <div class="hero-frame" style="left:260px;top:30px;width:200px;height:500px">
    <div class="screen" style="height:625px;transform:scale(.8)">
      <div class="screen-top"></div>
      <div class="status"><span>12:30PM</span><span class="status-icons"><i></i><i></i><i></i></span></div>
      <div class="appbar"><svg class="icon"><use href="#i-menu"/></svg><span class="title">Profile</span><svg class="icon"><use href="#i-bell"/></svg><span class="avatar" role="img" aria-label="User portrait"></span></div>
      <div class="ring-wrap"><svg viewBox="0 0 110 110"><circle cx="55" cy="55" r="48" fill="none" stroke="#e6eef6" stroke-width="6"/><circle cx="55" cy="55" r="48" fill="none" stroke="#00A9DD" stroke-width="6" stroke-dasharray="300 302" transform="rotate(-90 55 55)"/></svg><div class="ring-value"><b>200</b><small>Today Sugar<br>Bites</small></div></div>
      <div class="card" style="margin-top:18px"><div class="card-title">Why you want medicine free control</div><div class="reason">I want medicine-free control because I believe that relying solely on medication can have limitations and potential side effects.</div></div>
      <div class="pill"><i></i>Progress avg decrease 30 points</div>
      <div class="card"><div class="card-title">Life Spector</div><div class="chart"><div class="y-axis"><span>25</span><span>20</span><span>15</span><span>10</span><span>5</span></div><div class="chart-body"><svg viewBox="0 0 180 80"><use href="#line-chart"/></svg></div></div></div>
    </div>
  </div>
  <div class="hero-frame" style="left:480px;top:10px;width:240px;height:540px">
    <div class="screen" style="height:562px;transform:scale(.96)">
      <div class="screen-top"></div>
      <div class="status"><span>12:30PM</span><span class="status-icons"><i></i><i></i><i></i></span></div>
      <div class="appbar"><svg class="icon"><use href="#i-menu"/></svg><span class="title">Sugar Count</span><svg class="icon"><use href="#i-bell"/></svg><span class="avatar" role="img" aria-label="User portrait"></span></div>
      <div class="ring-wrap"><svg viewBox="0 0 110 110"><circle cx="55" cy="55" r="48" fill="none" stroke="#e6eef6" stroke-width="6"/><circle cx="55" cy="55" r="48" fill="none" stroke="#00A9DD" stroke-width="6" stroke-dasharray="225 302" transform="rotate(-90 55 55)"/></svg><div class="ring-value"><b>5</b><small>Sugar today<br>taken</small></div></div>
      <div class="heading" style="margin-top:28px">Consumption Today</div>
      <svg class="gauge"><use href="#gauge"/></svg>
      <nav class="nav"><span class="active"><svg><use href="#n-pie"/></svg></span><svg><use href="#n-cols"/></svg><svg><use href="#n-target"/></svg><svg><use href="#n-board"/></svg><svg><use href="#n-user"/></svg></nav>
    </div>
  </div>
  <div class="hero-frame" style="left:740px;top:30px;width:200px;height:500px">
    <div class="screen" style="height:625px;transform:scale(.8)">
      <div class="status"><span>12:30PM</span><span class="status-icons"><i></i><i></i><i></i></span></div>
      <div class="appbar"><svg class="icon"><use href="#i-menu"/></svg><span class="title">Rehab Monitor</span><svg class="icon"><use href="#i-bell"/></svg><span class="avatar" role="img" aria-label="User portrait"></span></div>
      <div class="card" style="margin-top:6px"><div class="card-title">Daily Sugar Graph</div><div class="chart"><div class="y-axis"><span>25</span><span>20</span><span>15</span><span>10</span><span>5</span></div><div class="chart-body"><svg viewBox="0 0 180 80"><use href="#line-chart"/></svg><div class="x-axis"><span>Mon</span><span>Tue</span><span>Wed</span><span>Thu</span><span>Fri</span><span>Sat</span><span>Sun</span></div></div></div></div>
      <div class="card"><div class="card-title">Daily Walk/Endres</div><div class="chart"><div class="y-axis"><span>8.5k</span><span>6.5k</span><span>4.5k</span><span>2.5k</span><span>1k</span></div><div class="chart-body"><svg viewBox="0 0 180 100"><use href="#bar-chart"/></svg><div class="x-axis"><span>Mon</span><span>Tue</span><span>Wed</span><span>Thu</span><span>Fri</span><span>Sat</span><span>Sun</span></div></div></div></div>
      <div class="stats"><div class="stat"><span class="stat-dot" style="background:var(--light)">25</span>Sugar bite<br>count weekly</div><div class="stat"><span class="stat-dot" style="background:var(--sky)">15</span>Weekly<br>Average</div></div>
      <div class="heading" style="margin-top:14px">Daily Feed</div>
    </div>
  </div>
  <div class="hero-frame" style="left:960px;top:60px;width:140px;height:440px">
    <div class="screen" style="height:786px;transform:scale(.56)">
      <div class="status"><span>12:30PM</span><span class="status-icons"><i></i><i></i><i></i></span></div>
      <div class="appbar"><svg class="icon"><use href="#i-menu"/></svg><span class="title">Rehab Plan</span><svg class="icon"><use href="#i-bell"/></svg><span class="avatar" role="img" aria-label="User portrait"></span></div>
      <div class="info-card"><span class="flame-badge"></span><span>See your plan to achieve,<br>no medicine diabetic control</span></div>
      <div class="sub">Create your plan in just few steps</div>
      <div class="stepper"><i class="done"></i><b class="done"></b><i class="now"></i><b></b><i></i><b></b><i></i><b></b><i></i><b></b><i></i></div>
      <div class="date-card">Choose desired Date<div class="date-field"><span>22 Mar 2025</span><svg class="icon"><use href="#n-board"/></svg></div></div>
      <div class="buttons" style="top:520px"><span class="btn btn-ghost">Prev</span><span class="btn btn-main">Next</span></div>
      <nav class="nav"><svg><use href="#n-pie"/></svg><svg><use href="#n-cols"/></svg><svg><use href="#n-target"/></svg><span class="active"><svg><use href="#n-board"/></svg></span><svg><use href="#n-user"/></svg></nav>
    </div>
  </div>
</div>

<!-- Row one -->
<div class="section-label" style="left:145px;top:1004px">SUGAR COUNT</div>
<div class="section-label" style="left:475px;top:1004px">REHAB COUNT</div>
<div class="section-label" style="left:795px;top:1004px">REHAB PLAN</div>

<section class="screen sugar-count" style="left:145px;top:1040px;height:545px">
  <div class="screen-top"></div>
  <div class="status"><span>12:30PM</span><span class="status-icons"><i></i><i></i><i></i></span></div>
  <div class="appbar"><svg class="icon"><use href="#i-menu"/></svg><span class="title">Sugar Count</span><svg class="icon"><use href="#i-bell"/></svg><span class="avatar" role="img" aria-label="User portrait"></span></div>
  <div class="ring-wrap"><svg viewBox="0 0 110 110"><circle cx="55" cy="55" r="48" fill="none" stroke="#e6eef6" stroke-width="6"/><circle cx="55" cy="55" r="48" fill="none" stroke="#00A9DD" stroke-width="6" stroke-dasharray="225 302" transform="rotate(-90 55 55)"/></svg><div class="ring-value"><b>5</b><small>Sugar today<br>taken</small></div></div>
  <div class="heading" style="margin-top:28px">Consumption Today</div>
  <svg class="gauge"><use href="#gauge"/></svg>
  <nav class="nav"><span class="active"><svg><use href="#n-pie"/></svg></span><svg><use href="#n-cols"/></svg><svg><use href="#n-target"/></svg><svg><use href="#n-board"/></svg><svg><use href="#n-user"/></svg></nav>
</section>

<section class="screen rehab-monitor" style="left:475px;top:1040px;height:880px">
  <div class="status"><span>12:30PM</span><span class="status-icons"><i></i><i></i><i></i></span></div>
  <div class="appbar"><svg class="icon"><use href="#i-menu"/></svg><span class="title">Rehab Monitor</span><svg class="icon"><use href="#i-bell"/></svg><span class="avatar" role="img" aria-label="User portrait"></span></div>
  <div class="card" style="margin-top:6px"><div class="card-title">Daily Sugar Graph</div><div class="chart"><div class="y-axis"><span>25</span><span>20</span><span>15</span><span>10</span><span>5</span></div><div class="chart-body"><svg viewBox="0 0 180 80"><use href="#line-chart"/></svg><div class="x-axis"><span>Mon</span><span>Tue</span><span>Wed</span><span>Thu</span><span>Fri</span><span>Sat</span><span>Sun</span></div></div></div></div>
  <div class="card"><div class="card-title">Daily Walk/Endres</div><div class="chart"><div class="y-axis"><span>8.5k</span><span>6.5k</span><span>4.5k</span><span>2.5k</span><span>1k</span></div><div class="chart-body"><svg viewBox="0 0 180 100"><use href="#bar-chart"/></svg><div class="x-axis"><span>Mon</span><span>Tue</span><span>Wed</span><span>Thu</span><span>Fri</span><span>Sat</span><span>Sun</span></div></div></div></div>
  <div class="stats"><div class="stat"><span class="stat-dot" style="background:var(--light)">25</span>Sugar bite<br>count weekly</div><div class="stat"><span class="stat-dot" style="background:var(--sky)">15</span>Weekly<br>Average</div></div>
  <div class="heading" style="margin:20px 0 16px">Daily Feed</div>
  <div class="feed"><div class="feed-label"><svg viewBox="0 0 14 14"><path d="M2 2l10 10M12 2L2 12M4 4h-2M10 10h2" stroke="currentColor" stroke-width="1.2" fill="none"/></svg>Fasting Sugar</div><div class="feed-field">90 <small>MG/DL</small></div></div>
  <div class="feed"><div class="feed-label"><svg viewBox="0 0 14 14"><rect x="2" y="6" width="5" height="5" fill="none" stroke="currentColor" stroke-width="1.1"/><rect x="7" y="6" width="5" height="5" fill="none" stroke="currentColor" stroke-width="1.1"/><rect x="4.5" y="1.5" width="5" height="4.5" fill="none" stroke="currentColor" stroke-width="1.1"/></svg>Random Sugar</div><div class="feed-field">120 <small>MG/DL</small></div></div>
  <div class="feed"><div class="feed-label"><svg viewBox="0 0 14 14"><path d="M3 12l4-5 4 3M7 7l1-4 3 2" stroke="currentColor" stroke-width="1.2" fill="none" stroke-linecap="round"/></svg>Daily Walk Time / Endres</div><div class="feed-field">5698 <small>Steps</small></div></div>
  <nav class="nav"><svg><use href="#n-pie"/></svg><span class="active"><svg><use href="#n-cols"/></svg></span><svg><use href="#n-target"/></svg><svg><use href="#n-board"/></svg><svg><use href="#n-user"/></svg></nav>
</section>

<section class="screen rehab-plan" style="left:795px;top:1040px;height:545px">
  <div class="status" style="margin-top:14px"><span>12:30PM</span><span class="status-icons"><i></i><i></i><i></i></span></div>
  <div class="appbar"><svg class="icon"><use href="#i-menu"/></svg><span class="title">Rehab Plan</span><svg class="icon"><use href="#i-bell"/></svg><span class="avatar" role="img" aria-label="User portrait"></span></div>
  <div class="info-card"><span class="flame-badge"></span><span>See your plan to achieve,<br>no medicine diabetic control</span></div>
  <div class="sub">Create your plan in just few steps</div>
  <div class="stepper"><i class="done"></i><b class="done"></b><i class="now"></i><b></b><i></i><b></b><i></i><b></b><i></i><b></b><i></i></div>
  <div class="date-card">Choose desired Date<div class="date-field"><span>22 Mar 2025</span><svg class="icon" style="color:var(--blue)"><use href="#n-board"/></svg></div></div>
  <div class="buttons" style="top:443px"><span class="btn btn-ghost">Prev</span><span class="btn btn-main">Next</span></div>
  <nav class="nav"><svg><use href="#n-pie"/></svg><svg><use href="#n-cols"/></svg><svg><use href="#n-target"/></svg><span class="active"><svg><use href="#n-board"/></svg></span><svg><use href="#n-user"/></svg></nav>
</section>

<!-- Row two -->
<div class="section-label" style="left:126px;top:2022px">REHAB PLAN - ONE</div>
<div class="section-label" style="left:490px;top:2022px">PROFILE</div>
<div class="section-label" style="left:805px;top:2022px">GOALS</div>

<section class="screen rehab-plan-one" style="left:146px;top:2075px;height:545px">
  <div class="status" style="margin-top:14px"><span>12:30PM</span><span class="status-icons"><i></i><i></i><i></i></span></div>
  <div class="appbar"><svg class="icon"><use href="#i-menu"/></svg><span class="title">Rehab Plan</span><svg class="icon"><use href="#i-bell"/></svg><span class="avatar" role="img" aria-label="User portrait"></span></div>
  <div class="sub" style="margin-top:18px;font-size:9.5px">Follow Suggested Diet</div>
  <div class="stepper" style="margin-bottom:22px"><i class="done"></i><b class="done"></b><i class="done"></i><b></b><i class="now"></i><b></b><i></i><b></b><i></i><b></b><i></i></div>
  <div class="diet"><span class="diet-photo" role="img" aria-label="Vegan meal photo" style="background:linear-gradient(135deg,#4d6b3a,#c9763a)"></span>Vegan Diet<span class="check on"></span></div>
  <div class="diet"><span class="diet-photo" role="img" aria-label="Carb meal photo" style="background:linear-gradient(135deg,#d0893f,#6b4a2e)"></span>Carb Diet<span class="check"></span></div>
  <div class="diet"><span class="diet-photo" role="img" aria-label="Keto meal photo" style="background:linear-gradient(135deg,#a24a36,#5f7a3d)"></span>Keto Diet<span class="check"></span></div>
  <div class="buttons" style="top:430px"><span class="btn btn-ghost">Prev</span><span class="btn btn-main">Next</span></div>
  <nav class="nav"><svg><use href="#n-pie"/></svg><svg><use href="#n-cols"/></svg><svg><use href="#n-target"/></svg><span class="active"><svg><use href="#n-board"/></svg></span><svg><use href="#n-user"/></svg></nav>
</section>

<section class="screen profile" style="left:490px;top:2060px;height:710px">
  <div class="screen-top"></div>
  <div class="status"><span>12:30PM</span><span class="status-icons"><i></i><i></i><i></i></span></div>
  <div class="appbar"><svg class="icon"><use href="#i-menu"/></svg><span class="title">Profile</span><svg class="icon"><use href="#i-bell"/></svg><span class="avatar" role="img" aria-label="User portrait"></span></div>
  <div class="ring-wrap"><svg viewBox="0 0 110 110"><circle cx="55" cy="55" r="48" fill="none" stroke="#e6eef6" stroke-width="6"/><circle cx="55" cy="55" r="48" fill="none" stroke="#00A9DD" stroke-width="6" stroke-dasharray="300 302" transform="rotate(-90 55 55)"/></svg><div class="ring-value"><b>200</b><small>Today Sugar<br>Bites</small></div></div>
  <div class="card" style="margin-top:18px"><div class="card-title">Why you want medicine free control</div><div class="reason">I want medicine-free control because I believe that relying solely on medication can have limitations and potential side effects.</div></div>
  <div class="pill"><i></i>Progress avg decrease 30 points</div>
  <div class="card"><div class="card-title">Life Spector</div><div class="chart"><div class="y-axis"><span>25</span><span>20</span><span>15</span><span>10</span><span>5</span></div><div class="chart-body"><svg viewBox="0 0 180 80"><use href="#line-chart"/></svg><div class="x-axis"><span>Mon</span><span>Tue</span><span>Wed</span><span>Thu</span><span>Fri</span><span>Sat</span><span>Sun</span></div></div></div></div>
  <nav class="nav"><svg><use href="#n-pie"/></svg><svg><use href="#n-cols"/></svg><svg><use href="#n-target"/></svg><svg><use href="#n-board"/></svg><span class="active"><svg><use href="#n-user"/></svg></span></nav>
</section>

<section class="screen goals" style="left:817px;top:2060px;height:560px">
  <div class="status"><span>12:30PM</span><span class="status-icons"><i></i><i></i><i></i></span></div>
  <div class="appbar"><svg class="icon"><use href="#i-menu"/></svg><span class="title">Goals</span><svg class="icon"><use href="#i-bell"/></svg><span class="avatar" role="img" aria-label="User portrait"></span></div>
  <div class="card" style="margin-top:10px"><div class="card-title">Days Until Goal</div><div class="mini-rings"><div class="mini"><div>10</div>Days</div><div class="mini"><div>5</div>Hour</div><div class="mini"><div>25</div>Mins</div><div class="mini"><div>50</div>Sec</div></div></div>
  <div class="card" style="padding:16px 10px"><div class="streak-ring"><div class="flame" role="img" aria-label="Flame illustration"></div></div><div class="streak-num">8</div><div class="streak-label">Days Streak</div><div class="best"><i></i>Your Best Streak : <b>20 Days</b></div></div>
  <nav class="nav"><span class="active"><svg><use href="#n-pie"/></svg></span><svg><use href="#n-cols"/></svg><svg><use href="#n-target"/></svg><svg><use href="#n-board"/></svg><svg><use href="#n-user"/></svg></nav>
</section>

<div class="thanks">THANK YOU FOR WATCHING MY WORKS</div>
</body>
</html>
```